July 2022 Industrial Manufacturer Product Expo Mexico City

We manufacture large screws and fastners for large Mining equipment, Trains, large ships, airplanes, wind turbines, and so on. We also do custom work base on the customer needs. No matter the size we can make it.
We have a Expo coming up with companies all over the world. We have to stand out we are a family own business so our customer service will be above and beyond anyone can provide. We do not have a sales force to push our products and services we provide one on one service.
Plus@!! I'm looking for anything that you designers can come up with if it was your company to put on a business card, plus i want to do a 1 or 2 sided pamphlet, and then a website. We make Speciality Bolts for large mining equipment these bolts can be 3 to 4 foot long!!! Plus fasteners, Nuts, washers, any, size, strengths, special materials, we offer more of a ono on one customer service, We are a small company, family own, but can fulfill any type of orders. We can also provide special time lines for emergency orders. "We keep the machines running we here at KRV don't believe in down time" We want to hear any slogan based on our company to stand out.
Thanks i really appreciate all your work and options that we have to pick on. Plus just a thought we could possibly want to entertain a experience Marketing internet help maybe a employment possibility. Thanks

I need 2 cards one in Spanish and English Like the steel back ground maybe send me in some bright red and blue writing Same with the Black cards Please remove the word Military The logo KRV maybe integrate a picture of a Bolt 🔩 Thank you

Still looking for I need 2 cards one in Spanish and English Like the steel back ground maybe send me in some bright red and blue writing Same with the Black cards try bright writing Please remove the word Military The logo KRV maybe integrate a picture of a Bolt 🔩 Plus will need the company to make a brochure and website next Thank you

Target Market(s)

Large Mining, Ship, Train, Green Energy, VELM, and Government equipment. Throughout the World

Industry/Entity Type

We can Custom Manufacture any type of Fastners for Mining equipment, Trains, Ships, Green energy, Governments, or military projects. wind turbines,

Contact Information for Business Card

I attached the name and contact info that's on a card, plus the Company Logo. Would like industrial looking background with Bright Colors that will stand out!! If we can insert somewhere maybe on back that we "Custom Manufacture Any Size or Quantity Fastners for Large Mining Equipment, Trains, Ships, Green Energy Equipment or Government Projects

Font styles to use
Other font styles liked:
• You Pick, has to be bold, colorful standout, Professional looking Beable to read it.

Colors

Designer to choose colors to be used in the design.

Requirements
Must have
• Need in Spanish and English TO STANDOUT FROM THE REST OF THE EXPO!! See Business card details, Rounded corners
Nice to have
• Can i see some of the darker cards with Bright Red and Blue letters I like to see the different type of card material, heavy thickness, plastic, transparent, Metal types, Bright Colors, I saw like Raised letters like on the logo.

```html
<!DOCTYPE html>
<html lang="es">
<head>
<meta charset="utf-8">
<title>KRV Business Card – English and Spanish Sides</title>
<link rel="stylesheet" href="https://fonts.googleapis.com/css2?family=Cormorant+SC:wght@600&family=Open+Sans:wght@400;600;700&display=swap">
<style>
  :root {
    --stage: #d9dadc;
    --paper: #ffffff;
    --charcoal: #2a2a2b;
    --ink-dark: #1d1d1f;
    --brand-blue: #0a7fd0;
    --navy: #12198a;
    --logo-grey: #3c3d40;
    --text-light: #ffffff;
  }
  * { box-sizing: border-box; margin: 0; padding: 0; }
  html, body { width: 1200px; height: 1015px; overflow: hidden; }
  body {
    background: var(--stage);
    position: relative;
    font-family: "Open Sans", Arial, sans-serif;
  }
  .card {
    position: absolute;
    width: 660px;
    height: 377px;
    background: var(--paper);
    border-radius: 14px;
    overflow: hidden;
    box-shadow: 0 6px 18px rgba(0,0,0,0.18);
  }
  .edge-strip {
    position: absolute;
    left: 0; right: 0; bottom: 0;
    height: 12px;
    display: flex;
  }
  .edge-strip .edge-dark { flex: 0 0 58%; background: var(--ink-dark); }
  .edge-strip .edge-blue { flex: 1; background: var(--brand-blue); }

  /* English side */
  .card-english { left: 50px; top: 70px; }
  .capabilities {
    position: absolute;
    left: 0; right: 0; top: 118px;
    text-align: center;
    font-family: "Cormorant SC", "Times New Roman", serif;
    font-weight: 600;
    font-size: 25px;
    line-height: 29px;
    color: var(--navy);
    letter-spacing: 0.5px;
  }

  /* Spanish side */
  .card-spanish { left: 490px; top: 520px; }
  .logo-area {
    position: absolute;
    left: 0; right: 0; top: 0;
    height: 132px;
    display: flex;
    align-items: center;
    justify-content: center;
    gap: 16px;
  }
  .logo-dot {
    width: 22px; height: 22px;
    border-radius: 50%;
    background: var(--brand-blue);
  }
  .logo-name {
    font-weight: 700;
    font-size: 74px;
    letter-spacing: 10px;
    color: var(--logo-grey);
  }
  .info-band {
    position: absolute;
    left: 0; right: 0; top: 142px;
    height: 160px;
    background: var(--charcoal);
    text-align: center;
    padding-top: 12px;
  }
  .person-name {
    font-weight: 700;
    font-size: 27px;
    color: var(--brand-blue);
    line-height: 36px;
  }
  .person-role, .person-email {
    font-size: 17px;
    color: var(--text-light);
    line-height: 23px;
  }
  .phones {
    margin-top: 16px;
    display: flex;
    justify-content: center;
    align-items: center;
    gap: 10px;
    font-size: 21px;
    color: var(--text-light);
    letter-spacing: 1px;
  }
  .phones svg { width: 22px; height: 22px; }
</style>
</head>
<body>

  <section class="card card-english" lang="en" aria-label="English side of the card">
    <p class="capabilities">
      Custom Manufacture Any Size or Quantity<br>
      Fastners for Large Mining Equipment<br>
      Trains, Ships, Green Energy Equipment<br>
      or Government Projects
    </p>
    <div class="edge-strip"><span class="edge-dark"></span><span class="edge-blue"></span></div>
  </section>

  <section class="card card-spanish" lang="es" aria-label="Lado en español de la tarjeta">
    <div class="logo-area">
      <span class="logo-dot"></span>
      <span class="logo-name">KRV</span>
    </div>
    <div class="info-band">
      <p class="person-name">Lic. Daniela Mireya Soto Vega</p>
      <p class="person-role">Cotizaciones en</p>
      <p class="person-email">ventas@krvtornilleria.mx</p>
      <div class="phones">
        <svg viewBox="0 0 24 24" aria-hidden="true"><path fill="#0a7fd0" d="M6.6 10.8a15.1 15.1 0 0 0 6.6 6.6l2.2-2.2c.3-.3.7-.4 1-.2 1.1.4 2.300.6 3.600.6.6 0 1 .4 1 1V20c0 .6-.4 1-1 1A17 17 0 0 1 3 4c0-.6.4-1 1-1h3.5c.6 0 1 .4 1 1 0 1.3.2 2.5.6 3.6.1.3 0 .7-.2 1z"/></svg>
        <span>5550142286</span>
        <svg viewBox="0 0 24 24" aria-hidden="true"><rect x="6" y="2" width="12" height="20" rx="2" fill="none" stroke="#0a7fd0" stroke-width="2.4"/><circle cx="12" cy="18" r="1.3" fill="#0a7fd0"/></svg>
        <span>5550193471</span>
      </div>
    </div>
    <div class="edge-strip"><span class="edge-dark"></span><span class="edge-blue"></span></div>
  </section>

</body>
</html>
```